Refresh of graphic design for existing website

We would like to refresh our website. Please see the attached design specifications.

Industry/Entity Type

Graphic Design

```html
<!DOCTYPE html>
<html lang="en">
<head>
<meta charset="utf-8">
<title>MSI — The Machinery and Service Institute</title>
<link href="https://fonts.googleapis.com/css2?family=Open+Sans:wght@400;600;700&display=swap" rel="stylesheet">
<style>
:root{
  --blue:#1f6fb5;
  --blue-dark:#14497a;
  --navy:#0d2c4a;
  --green:#5bab3c;
  --text:#555;
  --light:#f4f6f8;
  --line:#d9dee3;
}
*{box-sizing:border-box;margin:0;padding:0}
html,body{width:800px;height:1200px;overflow:hidden}
body{font-family:"Open Sans",Arial,sans-serif;color:var(--text);background:#fff;font-size:9px;position:relative}
.site-header{height:80px;display:flex;justify-content:space-between;align-items:center;padding:0 60px}
.brand{display:flex;align-items:center;gap:10px;color:var(--blue)}
.brand-name{font-size:34px;font-weight:700;line-height:1}
.brand-tag{font-size:14px;font-weight:600;align-self:flex-start;margin-top:6px}
.brand-dot{width:12px;height:12px;border-radius:50%;background:var(--blue)}
.login{display:grid;grid-template-columns:auto 90px;gap:3px 6px;font-size:8px;align-items:center}
.login input{height:12px;border:1px solid var(--line)}
.login-btn{background:var(--blue);color:#fff;font-size:8px;padding:2px 10px;justify-self:start}
.login-forgot{color:var(--blue)}
.main-nav{height:22px;background:var(--blue);display:flex;padding:0 60px}
.main-nav a,.footer-nav a{color:#fff;text-decoration:none;font-size:9px;padding:0 14px;line-height:22px}
.main-nav a.active{background:var(--green)}
.hero{position:relative;height:232px;background:linear-gradient(100deg,#8aa2b4 0%,#c9b49a 30%,#d8d3c8 50%,#7f99ad 100%)}
.mission{position:absolute;left:520px;top:20px;width:250px;background:rgba(31,111,181,.88);color:#fff;font-size:12px;line-height:1.45;padding:14px 16px}
.hero-caption{height:19px;background:var(--blue-dark);color:#fff;font-size:10px;line-height:19px;padding-left:60px}
.welcome{text-align:center;padding:14px 70px 0;height:148px}
h2{color:var(--blue);font-weight:400;font-size:19px;margin-bottom:8px}
.welcome p{font-size:8px;line-height:1.5;margin-bottom:6px}
.btn{display:inline-block;background:var(--blue);color:#fff;font-size:8px;padding:4px 12px;text-decoration:none}
.columns{display:flex;gap:14px;padding:0 60px;height:240px}
.panel{flex:1;border:1px solid var(--line)}
.panel h3{background:var(--blue);color:#fff;font-weight:400;font-size:13px;padding:6px 10px}
.panel ul{list-style:none;padding:6px 10px}
.panel li{border-bottom:1px solid var(--line);padding:5px 0;font-size:8px;line-height:1.4}
.name{color:var(--blue);font-weight:600}
.panel .more{color:var(--blue-dark);font-weight:600;font-size:8px;padding:4px 10px;display:block}
.panel p{font-size:8px;line-height:1.5;padding:8px 10px}
.panel strong{color:#333;font-size:9px;display:block;padding:8px 10px 0}
.quick{height:148px;margin-top:14px;background:linear-gradient(180deg,#2c2f33,#1b1d20 60%,#34383d);color:#ddd;text-align:center;padding-top:12px}
.quick h2{color:#fff}
.quick-grid{display:grid;grid-template-columns:repeat(4,1fr);gap:3px 20px;text-align:left;padding:0 90px;margin-bottom:8px}
.quick-grid span{font-size:8px;display:flex;align-items:center;gap:5px}
.quick-grid span::before{content:"";width:5px;height:5px;background:var(--green);border-radius:50%}
.upcoming{height:148px;text-align:center;padding-top:14px}
.events{display:flex;gap:30px;padding:0 90px;text-align:left;margin-bottom:10px}
.event{flex:1;font-size:8px;line-height:1.45}
.event .name{font-size:10px}
.subscribe{height:85px;background:linear-gradient(180deg,#23272c,#3a3f45);text-align:center;padding-top:8px;color:#fff}
.subscribe h2{color:#fff;margin-bottom:6px}
.sub-row{display:flex;justify-content:center;align-items:center;gap:10px;font-size:9px}
.sub-row .field{width:190px;height:16px;background:#fff}
.sub-row .btn{font-size:9px}
.site-footer{position:absolute;left:0;right:0;bottom:0;height:60px;background:var(--navy);text-align:center;padding-top:8px}
.footer-nav{display:flex;justify-content:center}
.footer-nav a{padding:0 10px}
.copyright{color:#9bb;font-size:7px}
</style>
</head>
<body>
<header class="site-header">
  <div class="brand"><span class="brand-dot"></span><span class="brand-name">MSI</span><span class="brand-tag">The Machinery and Service Institute</span></div>
  <form class="login">
    <span>User Name</span><input type="text">
    <span>Password</span><input type="password">
    <span></span><span><span class="login-btn">Login</span> <span class="login-forgot">Forgot Password?</span></span>
  </form>
</header>
<nav class="main-nav">
  <a class="active">Home</a><a>About MSI</a><a>Membership</a><a>MSI Events</a><a>TechLink Library</a><a>Market Research</a><a>Hidden Files</a>
</nav>
<section class="hero" role="img" aria-label="Smiling technician in a hard hat at an industrial site">
  <div class="mission">MSI's Mission is to advance the vehicle service industry by providing technical data and tools during the life of the vehicle, fostering the growth of transportation products, ensuring the efficiency and the provision of tools, equipment and service information.</div>
</section>
<div class="hero-caption">Advancing the vehicle service industry since 1947</div>
<section class="welcome">
  <h2>Welcome to MSI</h2>
  <p>MSI's Mission is to advance the vehicle service industry by providing technical data and tools during the life of the vehicle and products, and we foster the growth of transportation products through shared standards.</p>
  <p>MSI is one of the most respected trade associations in the automotive aftermarket, giving tool and equipment makers access to all segments of the service industry. Our members are innovators of service tools and equipment that keep vehicles safe.</p>
  <a class="btn">Read More</a>
</section>
<section class="columns">
  <div class="panel"><h3>Industry Events</h3>
    <ul>
      <li><span class="name">Dana Whitfield</span><br>11 Sep 2013 6:00 PM<br>Automakers commit to making automatic braking standard</li>
      <li><span class="name">Dana Whitfield</span><br>11 Sep 2013 6:00 PM<br>Automakers commit to making automatic braking standard</li>
      <li><span class="name">Dana Whitfield</span><br>11 Sep 2013 6:00 PM<br>Automakers commit to making automatic braking standard</li>
    </ul><span class="more">Learn More ›</span></div>
  <div class="panel"><h3>Breaking News</h3>
    <ul>
      <li><span class="name">Dana Whitfield</span><br>11 Sep 2013 6:00 PM<br>Automakers commit to making automatic braking standard</li>
      <li><span class="name">Dana Whitfield</span><br>11 Sep 2013 6:00 PM<br>Automakers commit to making automatic braking standard</li>
      <li><span class="name">Dana Whitfield</span><br>11 Sep 2013 6:00 PM<br>Automakers commit to making automatic braking standard</li>
    </ul><span class="more">Learn More ›</span></div>
  <div class="panel"><h3>Join MSI</h3>
    <strong>Member Benefits</strong>
    <p>Contribute to and shape service technology standards across the industry. The Summit gathers members, automakers and technicians each year to share training and resources. Our committees review data access so tool makers stay ready for new vehicle platforms.</p>
    <span class="more">Learn More ›</span></div>
</section>
<section class="quick" role="img" aria-label="Dark background photo of a vehicle service workshop">
  <h2>Quick Links</h2>
  <div class="quick-grid">
    <span>TechLink Library</span><span>MSI Member Participants</span><span>Industry Events Calendar</span><span>Membership</span>
    <span>Become a Member</span><span>Collaborative Workshops</span><span>Annual Summit Schedule</span><span>Market Research</span>
    <span>MSI Events</span><span>Tool and Equipment Forum</span><span>Technician Training Resources</span><span>Member Directory Downloads</span>
  </div>
  <a class="btn">Read More</a>
</section>
<section class="upcoming">
  <h2>Upcomming Events</h2>
  <div class="events">
    <div class="event"><span class="name">Dana Whitfield</span><br>11 Sep 2013 6:00 PM<br>Automakers commit to making automatic braking standard</div>
    <div class="event"><span class="name">Dana Whitfield</span><br>11 Sep 2013 6:00 PM<br>Automakers commit to making automatic braking standard</div>
    <div class="event"><span class="name">Dana Whitfield</span><br>11 Sep 2013 6:00 PM<br>Automakers commit to making automatic braking standard</div>
  </div>
  <a class="btn">Read More</a>
</section>
<section class="subscribe" role="img" aria-label="Dark background photo of service tools">
  <h2>Subscribe</h2>
  <div class="sub-row"><span>Lorem ipsum dolor sit amet conse ctetur adipiscing elit, sed do eiusmod tempor.</span><span class="field"></span><a class="btn">Subscribe</a></div>
</section>
<footer class="site-footer">
  <nav class="footer-nav"><a>Home</a><a>About MSI</a><a>Membership</a><a>MSI Events</a><a>TechLink Library</a><a>Market Research</a><a>Hidden Files</a></nav>
  <p class="copyright">Copyright © 2013. All Rights Reserved.</p>
</footer>
</body>
</html>
```